Web Design Velmora Tech

• An Overview of Velmora Tech for reference: We use to be a component manufacturing company. We sold to customers in USA and manage the builds in China using many manufacturing partners. We had a web site that served this market but we have transitioned over the last several years into “A unique design, development and program management company” It is this message we want to put up on the web now. We provide the design support, we help develop and test a new product for our customers and we provide the manufactured produce once we have transitioned it into production.
• The Target Market: Our customers are all high tech. Each product we produce is custom designed and sold only to one a specific customer. We work with a limited number of customer and sell to new customers by word of mouth and referrals. The web site is to provide a back ground check of any new referral so they can see who we are and our basic capabilities. It is not designed to sell customers or to find new customers but provide a background check to new potential customers.
• Pages Required: We estimate 12:
o Home/Title page is page 1 of PDF. It would have buttons to select other pages
o Names of other pages would be (short titles below if on button, if pull down menu the full title of slide)
 USA Facilities
 China Facilities
 Enclosures
 Antennas
 Connectors
 Cables
 EMI Shields
 Overlays
 Process Development
 BrisaLink
 Contact Us (???) >> new page which we are not sure if we should or should not add.
• Design Specifics; attached is our logo, a PDF and PowerPoint slides showing the views we desire. We like these layouts, but perhaps a better one may be suggested for some artistic reason or layout. It should be clean, simple and user intuitive. We like the off white background and use for most of our presentations. One should be able to go from any screen to any other screen. The quote must include both design and implementation onto our web site which is http://velmoratechworks.example/
• Design Process:
We would like to see concepts of the Landing/Homepage, and an internal page initially. Feedback will be provided and you will be asked to continue if your layout is on the correct track.

• Implementation: Desire designer/implimentor to set up on their server. Allow us to test and edit on their site. We will provide password for implementation on our site after final approval.

Target Market(s)

• The Target Market: see above task descripiton

Industry/Entity Type

It Company

Requirements
Must have
• • Pages Required: We estimate 12:
 USA Facilities
 China Facilities
 Enclosures
 Antennas
 Connectors
 Cables
 EMI Shields
 Overlays
 Process Development
 BrisaLink

Must have the implementation phase include in quote. see task description above
Should not have
• Should not be complex or long time loading.
Do not want any twitter or promotional add on functions.

```html
<!DOCTYPE html>
<html lang="en">
<head>
<meta charset="utf-8">
<title>Velmora Tech — Design, Development &amp; Program Management</title>
<link rel="stylesheet" href="https://fonts.googleapis.com/css2?family=Source+Sans+3:wght@400;600&display=swap">
<style>
:root{
  --blue:#0a6ebd;
  --blue-dark:#075a9c;
  --ink:#2b2b2b;
  --text:#3a3a3a;
  --rule:#e2e2e2;
  --footer:#3d3d3d;
  --footer-text:#b9b9b9;
  --page:#ffffff;
}
*{margin:0;padding:0;box-sizing:border-box}
html,body{width:1134px;height:1200px;overflow:hidden;background:var(--page)}
body{font-family:"Source Sans 3",sans-serif;color:var(--text);position:relative}
.site-header{position:absolute;left:0;top:0;width:1134px;height:119px}
.brand{position:absolute;left:113px;top:46px;display:flex;align-items:center;gap:10px;text-decoration:none}
.brand-mark{width:34px;height:34px;background:var(--blue)}
.brand-name{font-size:30px;font-weight:600;color:var(--blue);letter-spacing:.2px}
.search{position:absolute;left:759px;top:42px;width:255px;height:37px;border:1px solid #d6d6d6;box-shadow:inset 0 1px 3px rgba(0,0,0,.12);background:#fff}
.search svg{position:absolute;right:10px;top:10px}
.main-nav{position:absolute;left:0;top:119px;width:1134px;height:39px;background:var(--blue)}
.main-nav ul{list-style:none;display:flex;position:absolute;left:113px;top:0;height:39px}
.main-nav li{height:39px;line-height:39px;font-size:11.5px;font-weight:600;color:#fff;padding:0 8px;border-right:1px solid var(--blue-dark)}
.main-nav li:last-child{border-right:none}
.main-nav li:first-child{padding-left:7px}
.hero{position:absolute;left:0;top:158px;width:1134px;height:434px;background:linear-gradient(120deg,#5b5650 0%,#8a7a66 35%,#a98f6c 60%,#d9d6d0 100%)}
.hero-caption{position:absolute;left:113px;top:182px;width:477px;height:86px;background:var(--blue);color:#fff;font-size:28px;line-height:34px;padding:8px 9px;letter-spacing:.2px}
.hero-dots{position:absolute;left:121px;top:406px;display:flex;gap:6px}
.hero-dots span{width:8px;height:8px;border-radius:50%;background:rgba(255,255,255,.6)}
.hero-dots span:first-child{background:#fff}
.service{position:absolute;top:604px;width:284px}
.service h2{font-size:19px;font-weight:400;color:var(--ink);line-height:22px}
.service h3{font-size:17px;font-weight:400;color:var(--blue);line-height:21px}
.photo{display:block;width:284px;height:132px;margin-top:12px}
.body-copy{font-size:11.5px;line-height:17px;text-align:justify;margin-top:9px}
.read-more{position:absolute;font-size:12px;font-weight:600;color:var(--blue);text-decoration:none}
.divider{position:absolute;left:113px;top:927px;width:908px;height:1px;background:var(--rule)}
.section-title{position:absolute;top:940px;font-size:19px;font-weight:400;color:var(--blue)}
.welcome-photo{position:absolute;left:113px;top:979px;width:284px;height:132px;background:linear-gradient(135deg,#d9d5cc,#9c8a74 60%,#4a4a55)}
.welcome-copy{position:absolute;left:404px;top:976px;width:305px;font-size:11.5px;line-height:17px;text-align:justify}
.welcome-copy p+p{margin-top:17px}
.feature-copy{position:absolute;left:737px;top:976px;width:284px;font-size:11.5px;line-height:17px;text-align:justify}
.feature-copy p+p{margin-top:17px}
.site-footer{position:absolute;left:0;top:1153px;width:1134px;height:47px;background:var(--footer)}
.legal{position:absolute;left:113px;top:16px;font-size:11px;color:var(--footer-text)}
.legal span{margin:0 5px}
.social{position:absolute;left:914px;top:9px;display:flex;gap:10px}
.social span{width:28px;height:28px;border-radius:50%;background:#1a3fc4}
</style>
</head>
<body>
<header class="site-header">
  <a class="brand" href="http://velmoratechworks.example/"><span class="brand-mark"></span><span class="brand-name">Velmora Tech</span></a>
  <div class="search">
    <svg width="16" height="16" viewBox="0 0 16 16"><circle cx="6" cy="6" r="4" fill="none" stroke="#555" stroke-width="1.8"/><line x1="9" y1="9" x2="14" y2="14" stroke="#555" stroke-width="2.4"/></svg>
  </div>
</header>
<nav class="main-nav">
  <ul>
    <li>Home</li><li>USA Facilities</li><li>China Facilities</li><li>Enclosures</li><li>Antennas</li><li>Connectors</li><li>Cables</li><li>EMI Shields</li><li>Overlays</li><li style="padding:0 24px 0 16px">Process Development</li><li style="padding:0 12px 0 24px">BrisaLink</li><li style="padding:0 8px 0 13px">Contact Us</li>
  </ul>
</nav>
<section class="hero" role="img" aria-label="Engineers reviewing a red enclosure prototype at a table in front of a screen with CAD views">
  <div class="hero-caption">A UNIQUE DESIGN, DEVELOPMENT &amp;<br>PROGRAM MANAGEMENT COMPANY</div>
  <div class="hero-dots"><span></span><span></span><span></span><span></span></div>
</section>

<article class="service" style="left:112px">
  <h2>Enclosure</h2><h3>Design &amp; Development</h3>
  <div class="photo" role="img" aria-label="Engineers inspecting enclosure parts on a factory floor" style="background:linear-gradient(135deg,#b9b8ae,#5f6a55 55%,#c77a3a)"></div>
  <p class="body-copy">Lorem ipsum dolor sit amet, consectetur adipisicing elit, sed do eiusmod tempor incididunt ut labore et dolore magna aliqua. Ut enim ad minim veniam, quis nostrud exercitation ullamco laboris nisi ut aliquip ex ea commodo consequat.</p>
</article>
<a class="read-more" href="#" style="left:113px;top:894px">READ MORE</a>

<article class="service" style="left:424px">
  <h2>Antenna</h2><h3>Design &amp; Development</h3>
  <div class="photo" role="img" aria-label="Team meeting around a conference table with a presentation screen" style="background:linear-gradient(135deg,#e6e4de,#9aa0a8 50%,#3a3e46)"></div>
  <p class="body-copy">Lorem ipsum dolor sit amet, consectetur adipisicing elit, sed do eiusmod tempor incididunt ut labore et dolore magna aliqua. Ut enim ad minim veniam, quis nostrud exercitation ullamco laboris nisi ut aliquip ex ea commodo consequat.</p>
</article>
<a class="read-more" href="#" style="left:425px;top:894px">READ MORE</a>

<article class="service" style="left:736px">
  <h2>Connector</h2><h3>Design &amp; Development</h3>
  <div class="photo" role="img" aria-label="Technician working at a dispensing machine in a lab" style="background:linear-gradient(135deg,#eceae6,#b4b6b8 50%,#4a4c52)"></div>
  <p class="body-copy">Lorem ipsum dolor sit amet, consectetur adipisicing elit, sed do eiusmod tempor incididunt ut labore et dolore magna aliqua. Ut enim ad minim veniam, quis nostrud exercitation ullamco laboris nisi ut aliquip ex ea commodo consequat.</p>
</article>
<a class="read-more" href="#" style="left:737px;top:894px">READ MORE</a>

<div class="divider"></div>

<h2 class="section-title" style="left:112px">Welcome to Our Site!</h2>
<div class="welcome-photo" role="img" aria-label="Staff member working at a computer in the office"></div>
<div class="welcome-copy">
  <p>Lorem ipsum dolor sit amet, consectetur adipisicing elit, sed do eiusmod tempor incididunt ut labore et dolore magna aliqua. Ut enim ad minim veniam, quis nostrud exercitation ullamco laboris nisi ut aliquip ex ea commodo consequat.</p>
  <p>Lorem ipsum dolor sit amet, consectetur adipisicing elit, sed do eiusmod tempor incididunt ut labore et dolore magna aliqua. Ut enim ad minim veniam, quis nostrud</p>
</div>
<a class="read-more" href="#" style="left:113px;top:1127px">READ MORE</a>

<h2 class="section-title" style="left:736px">Automated adhesive application</h2>
<div class="feature-copy">
  <p>With BrisaLink, Velmora Tech’s cloud based inventory and order processing system, you’ll have unprecedented real-time access to your critical order and inventory dataWith BrisaLink, Velmora Tech’s cloud based inventory and order processing system,</p>
  <p>you’ll have unprecedented real-time access to your critical order and inventory data</p>
</div>
<a class="read-more" href="#" style="left:737px;top:1127px">READ MORE</a>

<footer class="site-footer">
  <p class="legal">© 2013 velmora tech | All Rights Reserved <span>|</span>Contact Us<span>|</span>terms</p>
  <div class="social"><span></span><span></span><span></span></div>
</footer>
</body>
</html>
```